Business Card Design

Online clothing womens clothing store, I sell my clothing online and at the markets.

i would like the attached picture on the front of the card and the contact information on the back.

Industry/Entity Type

Business

Contact Information for Business Card

Marlow Thread
Karen Whitfield
(Instagram symbol) _marlow_thread_
(Facebook symbol) www.fakebookexample.com/marlowthreadau/

W : www.marlowthread.example.au
E : info@marlowthread.example.au
P : 0498716204

```html
<!DOCTYPE html>
<html lang="en">
<head>
<meta charset="utf-8">
<title>Marlow Thread – Business Card</title>
<link rel="stylesheet" href="https://fonts.googleapis.com/css2?family=Barlow:wght@300&family=Barlow+Condensed:wght@700&family=Open+Sans:wght@400&display=swap">
<style>
  :root {
    --page-bg: #e9e7e3;
    --card-white: #ffffff;
    --band-blue: #4746d4;
    --band-blue-light: #6a6ad6;
    --border-blue: #3434c4;
    --ink: #1a1a1a;
    --photo-light: #d9dcde;
    --photo-mid: #a9afb5;
    --photo-dark: #5f6a72;
    --mark-white: #f4f4f4;
  }
  * { box-sizing: border-box; margin: 0; padding: 0; }
  html, body { width: 1200px; height: 892px; overflow: hidden; }
  body {
    background: var(--page-bg);
    display: flex;
    flex-direction: column;
    align-items: center;
    justify-content: center;
    gap: 34px;
  }
  .card {
    position: relative;
    width: 680px;
    height: 389px;
    box-shadow: 0 4px 14px rgba(0,0,0,0.18);
    overflow: hidden;
  }

  /* Front */
  .card-front {
    background: var(--border-blue);
    padding: 9px;
  }
  .front-photo {
    position: absolute;
    inset: 9px;
    background:
      radial-gradient(ellipse 45% 60% at 62% 70%, var(--photo-dark) 0%, var(--photo-mid) 55%, transparent 80%),
      linear-gradient(180deg, var(--photo-light) 0%, #cfd3d6 50%, var(--photo-mid) 100%);
  }
  .front-name-thin {
    position: absolute;
    left: 56px;
    top: 122px;
    font-family: "Barlow", sans-serif;
    font-weight: 300;
    font-size: 50px;
    letter-spacing: 9px;
    color: var(--ink);
    text-transform: uppercase;
    white-space: nowrap;
  }
  .front-name-bold {
    position: absolute;
    left: 48px;
    top: 210px;
    font-family: "Barlow Condensed", sans-serif;
    font-weight: 700;
    font-size: 92px;
    letter-spacing: 3px;
    color: var(--mark-white);
    text-transform: uppercase;
    white-space: nowrap;
  }

  /* Back */
  .card-back { background: var(--card-white); }
  .back-band {
    position: absolute;
    left: 0; right: 0; bottom: 0;
    height: 62px;
    background: linear-gradient(90deg, var(--band-blue-light) 0%, var(--band-blue) 60%, var(--border-blue) 100%);
  }
  .back-band-rule {
    position: absolute;
    left: 0; right: 0; bottom: 66px;
    height: 3px;
    background: var(--ink);
  }
  .back-wordmark {
    position: absolute;
    left: 30px;
    top: 34px;
    font-family: "Barlow", sans-serif;
    font-weight: 300;
    font-size: 26px;
    letter-spacing: 6px;
    color: var(--ink);
    text-transform: uppercase;
    white-space: nowrap;
  }
  .back-divider {
    position: absolute;
    left: 372px;
    top: 176px;
    width: 2px;
    height: 142px;
    background: var(--ink);
  }
  .back-divider::after {
    content: "";
    position: absolute;
    left: -160px;
    bottom: 0;
    width: 160px;
    height: 2px;
    background: var(--ink);
  }
  .contact-block {
    position: absolute;
    left: 392px;
    top: 130px;
    font-family: "Open Sans", sans-serif;
    color: var(--ink);
  }
  .contact-name {
    font-size: 33px;
    line-height: 1.1;
    margin-bottom: 10px;
    white-space: nowrap;
  }
  .contact-list { list-style: none; }
  .contact-item {
    display: flex;
    align-items: center;
    gap: 10px;
    font-size: 16px;
    line-height: 25px;
    white-space: nowrap;
  }
  .contact-icon {
    width: 17px;
    height: 17px;
    flex: none;
  }
</style>
</head>
<body>

  <section class="card card-front" aria-label="Card front">
    <div class="front-photo" role="img" aria-label="Soft grey photograph of a woman in clothing, background for the brand name"></div>
    <div class="front-name-thin">Marlow Thread</div>
    <div class="front-name-bold">Marlow Thread</div>
  </section>

  <section class="card card-back" aria-label="Card back">
    <div class="back-wordmark">Marlow Thread</div>
    <div class="back-divider"></div>
    <div class="contact-block">
      <div class="contact-name">Karen Whitfield</div>
      <ul class="contact-list">
        <li class="contact-item">
          <svg class="contact-icon" viewBox="0 0 17 17" aria-hidden="true">
            <rect width="17" height="17" rx="2" fill="#1a1a1a"/>
            <path d="M5 4 L7 4 L8 6.5 L6.8 7.5 Q7.8 9.5 9.5 10.2 L10.5 9 L13 10 L13 12 Q12.5 13 11 13 Q4 12 4 5 Q4 4 5 4 Z" fill="#fff"/>
          </svg>
          0498716204
        </li>
        <li class="contact-item">
          <svg class="contact-icon" viewBox="0 0 17 17" aria-hidden="true">
            <rect width="17" height="17" rx="2" fill="#1a1a1a"/>
            <rect x="3.5" y="5" width="10" height="7" fill="none" stroke="#fff" stroke-width="1.2"/>
            <path d="M3.5 5 L8.5 9 L13.5 5" fill="none" stroke="#fff" stroke-width="1.2"/>
          </svg>
          info@marlowthread.example.au
        </li>
        <li class="contact-item">
          <svg class="contact-icon" viewBox="0 0 17 17" aria-hidden="true">
            <rect width="17" height="17" rx="2" fill="#1a1a1a"/>
            <circle cx="8.5" cy="8.5" r="5" fill="none" stroke="#fff" stroke-width="1.2"/>
            <ellipse cx="8.5" cy="8.5" rx="2" ry="5" fill="none" stroke="#fff" stroke-width="1"/>
            <line x1="3.5" y1="8.5" x2="13.5" y2="8.5" stroke="#fff" stroke-width="1"/>
          </svg>
          www.marlowthread.example.au
        </li>
        <li class="contact-item">
          <svg class="contact-icon" viewBox="0 0 17 17" aria-hidden="true">
            <rect x="1" y="1" width="15" height="15" rx="2" fill="none" stroke="#1a1a1a" stroke-width="1.6"/>
          </svg>
          _marlow_thread_
        </li>
        <li class="contact-item">
          <svg class="contact-icon" viewBox="0 0 17 17" aria-hidden="true">
            <rect width="17" height="17" rx="2" fill="#1a1a1a"/>
          </svg>
          www.fakebookexample.com
        </li>
      </ul>
    </div>
    <div class="back-band-rule"></div>
    <div class="back-band"></div>
  </section>

</body>
</html>
```